R7M Horizon Business Card Design

We need a business card created for our New Business "R7M Horizon"<br/><br/>The business card design is up to you however the following information must be on the business card:<br/><br/>Front of the business card -<br/>Email :darrenp@r7mhorizon.nz<br/>Mobile: +64 (0) 22 4870 619<br/>Website: www.r7mhorizon.nz<br/>Card Owner Name: Darren Paltrow<br/>Company Title: Business Development Manager<br/>Slogan: "The BEST of both worlds". <br/>Logo On the front attached to the design brief<br/><br/>On the back: <br/>Space on the back for 4 more versions of the logo across the bottom of the card indicating different subsidiary brands - R7M Coffee, R7M Arts, R7M ?? (The card will be used for all of these brands - We Will add the extra subsidiary logos to the design once the design is finished (We are a graphics design team). <br/><br/>Other than that we want a premium feeling logo that remains universally usable depending on the business entity that we are using the card for. The use of bright bold colours would be great but we still want the card to feel premium.
Target Market(s)
Gift Design and Manufacturing Companies
Contact Information for Business Card
Front of the business card -
Email :darrenp@r7mhorizon.nz
Mobile: +64 (0) 22 4870 619
Website: www.r7mhorizon.nz
Card Owner Name: Darren Paltrow
Company Title: Business Development Manager
Slogan: "The BEST of both worlds".
Logo On the front attached to the design brief

```html
<!DOCTYPE html>
<html lang="en">
<head>
<meta charset="utf-8">
<title>R7M Horizon Business Card</title>
<link href="https://fonts.googleapis.com/css2?family=Exo+2:wght@400;600;700&family=Open+Sans:wght@400;600&display=swap" rel="stylesheet">
<style>
  :root {
    --stage: #1c1c1e;
    --card: #262628;
    --card-deep: #2b2b2d;
    --edge: #3a4cc8;
    --brand-blue: #3446a8;
    --band-blue: #3447a6;
    --ink-light: #f2f2f5;
    --ghost: #323236;
    --ghost-ring: #2e3046;
  }
  * { box-sizing: border-box; margin: 0; padding: 0; }
  html, body { width: 1200px; height: 900px; overflow: hidden; }
  body {
    background: var(--stage);
    display: flex;
    flex-direction: column;
    align-items: center;
    justify-content: center;
    gap: 40px;
  }
  .card {
    position: relative;
    width: 700px;
    height: 400px;
    background: var(--card);
    border-left: 3px solid var(--edge);
    border-bottom: 3px solid var(--edge);
    overflow: hidden;
  }

  /* Back side */
  .card-back .ring {
    position: absolute;
    left: 50%;
    top: 50%;
    width: 320px;
    height: 320px;
    margin: -160px 0 0 -160px;
    border: 4px solid var(--ghost-ring);
    border-radius: 50%;
  }
  .card-back .brand-name {
    position: absolute;
    left: 0; right: 0;
    top: 50%;
    transform: translateY(-50%);
    text-align: center;
    font-family: "Exo 2", sans-serif;
    font-weight: 700;
    font-size: 48px;
    color: var(--ghost);
    letter-spacing: 1px;
  }

  /* Front side */
  .card-front .brand-name {
    position: absolute;
    left: 42px;
    top: 160px;
    font-family: "Exo 2", sans-serif;
    font-weight: 700;
    font-size: 40px;
    color: var(--brand-blue);
    letter-spacing: 0.5px;
  }
  .holder {
    position: absolute;
    left: 420px;
    top: 58px;
  }
  .holder-name {
    font-family: "Exo 2", sans-serif;
    font-weight: 700;
    font-size: 26px;
    color: var(--brand-blue);
    text-transform: uppercase;
    letter-spacing: 0.5px;
    line-height: 1.1;
  }
  .holder-title {
    font-family: "Open Sans", sans-serif;
    font-size: 17px;
    color: var(--ink-light);
    margin-top: 2px;
  }
  .contact-band {
    position: absolute;
    left: 345px;
    right: 0;
    top: 150px;
    height: 118px;
    background: var(--band-blue);
    border-radius: 59px 0 0 59px;
    padding: 14px 0 0 52px;
  }
  .contact-line {
    display: flex;
    align-items: center;
    gap: 12px;
    font-family: "Open Sans", sans-serif;
    font-size: 18px;
    color: var(--ink-light);
    line-height: 30px;
  }
  .contact-line svg { width: 16px; height: 16px; flex: none; }
  .slogan {
    position: absolute;
    left: 395px;
    bottom: 28px;
    font-family: "Exo 2", sans-serif;
    font-size: 22px;
    color: var(--brand-blue);
    text-transform: uppercase;
  }
</style>
</head>
<body>
  <section class="card card-back" aria-label="Card back">
    <div class="ring"></div>
    <div class="brand-name">R7M Horizon</div>
  </section>

  <section class="card card-front" aria-label="Card front">
    <div class="brand-name">R7M Horizon</div>

    <div class="holder">
      <div class="holder-name">Darren Paltrow</div>
      <div class="holder-title">Business Development Manager</div>
    </div>

    <div class="contact-band">
      <div class="contact-line">
        <svg viewBox="0 0 16 16" fill="none" stroke="#f2f2f5" stroke-width="1.3"><path d="M4 2l2.5 3-1.5 1.5c.8 1.8 2.2 3.2 4 4L10.5 9l3 2.5-1.5 2C7 13 3 9 2.5 3.5z"/></svg>
        <span>+64 (0) 22 4870 619</span>
      </div>
      <div class="contact-line">
        <svg viewBox="0 0 16 16" fill="none" stroke="#f2f2f5" stroke-width="1.3"><rect x="1.5" y="3.5" width="13" height="9"/><path d="M1.5 3.5l6.5 5 6.5-5"/></svg>
        <span>darrenp@r7mhorizon.nz</span>
      </div>
      <div class="contact-line">
        <svg viewBox="0 0 16 16" fill="none" stroke="#f2f2f5" stroke-width="1.3"><circle cx="8" cy="8" r="6.5"/><ellipse cx="8" cy="8" rx="3" ry="6.5"/><path d="M1.5 8h13"/></svg>
        <span>www.r7mhorizon.nz</span>
      </div>
    </div>

    <div class="slogan">The Best of Both Worlds</div>
  </section>
</body>
</html>
```